Modern web-site for a game changer new health app!

We need a very clean UX / UI design for our company website that will be used to sell our brand to large corporations and their employees. If we find a good match, we'd need you to do the app design and some graphics for ongoing design needs.

For a first of its kind app developed at Brockwell University, making licensed holistic medicine accessible to everyday people through access and curation by democratizing holistic health.

Please read the details attached thoroughly and reach out if you have any questions. Many thanks!
Updates

I've updated our requirements to make it easier, please review new details in the PDF shared. Many thanks!

Final brief refinement just uploaded, much has been simplified with very clear guidelines, please update and apply. thanks much!

Target Market(s)

corporate employees and large C level corporate leaders

Industry/Entity Type

wellness

Number of Pages Required

4 page

Font styles to use
Other font styles liked:
• We need website design now and app and socials after, hoping the designer we choose now can work with us on a regular basis going forward

Requirements
Must have
• clean, modern, minimal rich
Nice to have
• some added touches to give a custom feel
Should not have
• pictures, natural looking images or shapes

```html
<!DOCTYPE html>
<html lang="en">
<head>
<meta charset="utf-8">
<title>Oruna — Health For Everyone</title>
<link rel="stylesheet" href="https://fonts.googleapis.com/css2?family=Lexend:wght@300;400;500;600&family=Roboto:wght@400;500&display=swap">
<style>
:root{
  --ink:#0d0b08;
  --cream:#fdf1d6;
  --gold:#f5a800;
  --amber:#e88410;
  --orange:#d96a06;
  --rust:#c44d08;
  --mustard:#d99a0a;
  --card:#3a2f26;
  --text:#3b332b;
  --white:#ffffff;
  --btn:linear-gradient(180deg,#f7a21b,#d9620a);
}
*{box-sizing:border-box;margin:0;padding:0}
html,body{width:1200px;height:5021px;overflow:hidden}
body{position:relative;background:var(--ink);font-family:"Lexend",sans-serif;color:var(--text)}
.abs{position:absolute}
.dark{position:absolute;left:0;width:1200px;background:radial-gradient(ellipse at 70% 40%,#2b3526 0%,#141812 45%,#050505 100%)}
.cream{position:absolute;left:0;width:1200px;background:var(--cream)}
.band{position:absolute;left:0;width:1200px;height:46px;background:linear-gradient(90deg,#c96a08,#e0a063 20%,#f6cf8a 35%,#c96a08 50%,#e0a063 70%,#f6cf8a 85%,#c96a08)}
.btn{position:absolute;display:flex;align-items:center;justify-content:center;background:var(--btn);color:#fff;border-radius:22px;font-family:"Roboto",sans-serif;font-weight:500;font-size:14px;border:1.5px solid #ffd27a}
.leaf{position:absolute;width:10px;height:14px;border-radius:0 100% 0 100%;background:var(--gold)}
h1,h2{font-family:"Lexend",sans-serif;font-weight:600}
.h2{position:absolute;font-size:44px;line-height:60px;color:#1d1a16;font-weight:600}
.h2.light{color:#fff}
.logo{position:absolute;display:flex;align-items:center;gap:10px}
.logo .dot{border-radius:50%;background:var(--amber)}
.logo .name{font-family:"Lexend",sans-serif;font-weight:600;color:var(--amber);letter-spacing:2px}
.nav a{position:absolute;top:40px;color:#fff;font-size:15px;text-decoration:none;font-family:"Lexend",sans-serif;font-weight:300}
.feature{position:absolute;top:393px;width:312px;height:289px;background:var(--card);border-radius:26px;text-align:center;color:#fff}
.feature .ico{position:absolute;left:102px;top:40px;width:108px;height:108px;border-radius:50%;background:linear-gradient(180deg,#f7a21b,#d9620a);border:3px solid #ffd27a;display:flex;align-items:center;justify-content:center}
.feature p{position:absolute;top:185px;left:0;width:100%;font-family:"Roboto",sans-serif;font-weight:500;font-size:18px;line-height:26px}
.step{position:absolute;top:852px;width:116px;height:116px;border-radius:50%;background:#fff;display:flex;align-items:center;justify-content:center;box-shadow:0 4px 14px rgba(0,0,0,.06)}
.step-label{position:absolute;top:990px;width:240px;text-align:center;font-family:"Roboto",sans-serif;font-size:20px;line-height:26px;color:#1d1a16}
.pill{position:absolute;top:1591px;width:226px;height:330px;border-radius:113px;text-align:center}
.pill .disc{position:absolute;left:29px;top:22px;width:168px;height:168px;border-radius:50%;background:#fbf0dc;border:4px solid rgba(255,255,255,.6);display:flex;align-items:center;justify-content:center}
.pill span{position:absolute;top:231px;left:0;width:100%;color:#fff;font-family:"Roboto",sans-serif;font-weight:500;font-size:21px}
.body{position:absolute;font-weight:300;font-size:18px;line-height:29px}
.quote{position:absolute;top:3647px;width:473px;height:253px;background:#fff;border-radius:32px;box-shadow:0 6px 20px rgba(0,0,0,.05)}
.quote .avatar{position:absolute;left:28px;top:22px;width:62px;height:62px;border-radius:50%;background:linear-gradient(135deg,#c9b39a,#6f5a46)}
.quote h3{position:absolute;left:110px;top:22px;font-weight:400;font-size:21px;color:#1d1a16}
.quote time{position:absolute;left:110px;top:58px;font-size:16px;font-weight:300;color:#3b332b}
.quote p{position:absolute;left:40px;top:103px;width:410px;font-size:15px;line-height:26px;font-weight:300;color:#4a4038}
.arrow{position:absolute;top:3780px;width:20px;height:30px}
.field{position:absolute;left:580px;width:462px;height:42px;background:#f5f3ef;border:1px solid #ddd;border-radius:3px;padding:12px 20px;font-size:13px;color:#7a746c;font-weight:300}
.social{position:absolute;top:4910px;width:30px;height:30px;border-radius:50%;border:1.5px solid #fff}
</style>
</head>
<body>

<!-- HERO -->
<div class="dark" style="top:0;height:623px" role="img" aria-label="Dark photograph of white blossoms on a leafy branch"></div>
<div class="logo" style="left:113px;top:28px">
  <span class="dot" style="width:48px;height:48px"></span>
  <span class="name" style="font-size:36px">ORUNA</span>
</div>
<nav class="nav">
  <a style="left:443px;color:var(--gold)">Home</a>
  <a style="left:539px">Complementary</a>
  <a style="left:708px">Enterprise</a>
  <a style="left:836px">Members</a>
</nav>
<a class="btn" style="left:931px;top:25px;width:154px;height:43px">Get Started</a>

<h1 class="abs" style="left:0;top:128px;width:1200px;text-align:center;font-size:66px;line-height:80px;color:var(--gold);font-weight:600">Health For Everyone</h1>
<p class="abs" style="left:0;top:216px;width:1200px;text-align:center;color:#fff;font-size:18px;line-height:27px;font-weight:300">All-Inclusive Holistic Wellness &nbsp;$25 / month Time tested science<br>changing the lives of millions at a price everyone can afford.</p>
<a class="btn" style="left:522px;top:302px;width:156px;height:41px">Get Started</a>

<div class="band" style="top:578px" role="img" aria-label="Decorative band of triangles and half circles in orange and tan"></div>
<div class="cream" style="top:624px;height:623px"></div>

<div class="feature" style="left:113px">
  <div class="ico"><svg width="56" height="56" viewBox="0 0 56 56" fill="none" stroke="#fff" stroke-width="2.5"><path d="M28 48V22M28 30c-8 0-12-6-12-12 6 0 12 4 12 12zM28 30c8 0 12-6 12-12-6 0-12 4-12 12zM10 48h36"/></svg></div>
  <p>1 on 1 with Holistic<br>Doctors &amp; Unlimited</p>
</div>
<div class="feature" style="left:444px">
  <div class="ico"><svg width="56" height="56" viewBox="0 0 56 56" fill="none" stroke="#fff" stroke-width="2.5"><rect x="12" y="18" width="22" height="30" rx="3"/><rect x="14" y="10" width="18" height="8"/><rect x="34" y="30" width="12" height="18" rx="2"/><path d="M17 30h12M17 36h12"/></svg></div>
  <p>Personalized Custom<br>Supplements</p>
</div>
<div class="feature" style="left:775px">
  <div class="ico"><svg width="56" height="56" viewBox="0 0 56 56" fill="none" stroke="#fff" stroke-width="2.5"><circle cx="28" cy="28" r="8"/><circle cx="28" cy="10" r="4"/><circle cx="28" cy="46" r="4"/><circle cx="10" cy="28" r="4"/><circle cx="46" cy="28" r="4"/><path d="M28 14v6M28 36v6M14 28h6M36 28h6"/></svg></div>
  <p>Gut, Hormone &amp; Cellular<br>Lab Tests</p>
</div>

<!-- HOW IT WORKS -->
<span class="leaf" style="left:115px;top:770px"></span>
<h2 class="h2" style="left:113px;top:782px">How It Works</h2>
<p class="body" style="left:113px;top:862px;width:380px;font-size:18px;line-height:27px">Sign-up and get a full read of your unique constitution and what makes it thrive with a custom plan made one on one with your on-demand holistic Doctor/Educator. Unlimited texting to address your plan or any other concern you have about your health.</p>
<a class="btn" style="left:113px;top:1085px;width:154px;height:41px">View Plans</a>

<svg class="abs" style="left:640px;top:890px" width="340" height="40"><path d="M6 10 C50 40 90 40 110 30M220 14 C250 0 300 0 320 10" stroke="#c44d08" stroke-width="1.5" stroke-dasharray="5 4" fill="none"/></svg>
<div class="step" style="left:530px"><svg width="70" height="70" viewBox="0 0 70 70" fill="none" stroke="#1d1a16" stroke-width="3"><circle cx="32" cy="38" r="26"/><circle cx="32" cy="32" r="9"/><path d="M16 54c4-9 28-9 32 0M52 8v16M44 16h16"/></svg></div>
<div class="step" style="left:743px"><svg width="70" height="70" viewBox="0 0 70 70" fill="none" stroke="#1d1a16" stroke-width="3"><path d="M14 10h34v50H14zM14 10c-6 0-6 8 0 8M20 24h22M20 32h22M20 40h14M46 50l12-22 4 2-12 22z"/></svg></div>
<div class="step" style="left:961px"><svg width="70" height="70" viewBox="0 0 70 70" fill="none" stroke="#1d1a16" stroke-width="3"><rect x="10" y="12" width="36" height="48" rx="3"/><path d="M18 24h6M18 34h6M18 44h6M28 24h12M28 34h12M28 44h8"/><circle cx="46" cy="46" r="10"/><path d="M56 8v22"/></svg></div>
<p class="step-label" style="left:468px">Sign Up</p>
<p class="step-label" style="left:681px">Get a full read<br>of your constitution</p>
<p class="step-label" style="left:899px">Get a Custom<br>plan</p>

<div class="band" style="top:1247px" role="img" aria-label="Decorative band of triangles and half circles in orange and tan"></div>

<!-- TRUST -->
<div class="dark" style="top:1292px;height:916px" role="img" aria-label="Dark photograph of white blossoms and green leaves"></div>
<span class="leaf" style="left:594px;top:1404px"></span>
<h2 class="h2 light" style="left:0;top:1425px;width:1200px;text-align:center;font-size:43px;line-height:56px">Our Clients Trust Us to Provide Holistic<br>Health for Their Team, So Should You!</h2>

<div class="pill" style="left:208px;background:var(--mustard)">
  <div class="disc"><svg width="110" height="110" viewBox="0 0 110 110" fill="none" stroke="#6b5a45" stroke-width="1.5"><circle cx="55" cy="55" r="48"/><circle cx="55" cy="55" r="20"/><circle cx="55" cy="35" r="20"/><circle cx="55" cy="75" r="20"/><circle cx="35" cy="55" r="20"/><circle cx="75" cy="55" r="20"/></svg></div>
  <span>Any Challenge</span>
</div>
<div class="pill" style="left:487px;background:var(--rust)">
  <div class="disc"><svg width="110" height="110" viewBox="0 0 110 110" fill="none" stroke="#3b332b" stroke-width="2"><circle cx="55" cy="55" r="48" stroke-dasharray="2 4"/><circle cx="55" cy="55" r="38"/><path d="M55 55V28M55 55h20" stroke-width="3"/></svg></div>
  <span>Anytime</span>
</div>
<div class="pill" style="left:765px;background:var(--amber)">
  <div class="disc"><svg width="110" height="110" viewBox="0 0 110 110" fill="none" stroke="#6b5a45" stroke-width="2"><circle cx="55" cy="55" r="48"/><circle cx="55" cy="55" r="30"/><ellipse cx="55" cy="55" rx="14" ry="30"/><path d="M25 55h60M30 40h50M30 70h50"/></svg></div>
  <span>Anywhere</span>
</div>

<p class="abs" style="left:0;top:1994px;width:1200px;text-align:center;color:#fff;font-size:26px;font-weight:300">Trusted by:</p>
<p class="abs" style="left:0;top:2035px;width:1200px;text-align:center;color:#fff;font-size:52px;font-weight:600">Northfield Outfitters</p>

<div class="band" style="top:2207px" role="img" aria-label="Decorative band of triangles and half circles in orange and tan"></div>

<!-- ENTERPRISE -->
<div class="cream" style="top:2253px;height:540px"></div>
<span class="leaf" style="left:120px;top:2320px"></span>
<h2 class="h2" style="left:113px;top:2345px">Oruna for Enterprise</h2>
<p class="body" style="left:113px;top:2428px;width:760px">We’re all feeling a strain on our health these days<br>Leaders of industry aren’t accidental, they know employee retention &amp;<br>experience work in their favor.<br><br>IIn these tumultuous times, Veridia brings much-needed relief and benefits<br>to teams that bring their all in return.</p>
<a class="btn" style="left:113px;top:2643px;width:234px;height:41px">Oruna For Enterprise</a>

<div class="band" style="top:2792px" role="img" aria-label="Decorative band of triangles and half circles in orange and tan"></div>

<!-- HUMAN CARE -->
<div class="dark" style="top:2838px;height:523px;background:radial-gradient(circle at 70% 55%,#dfe3dc 0 7%,#2a3524 14%,#0a0c09 45%,#000 100%)" role="img" aria-label="Photograph of a single white blossom against a dark background"></div>
<span class="leaf" style="left:115px;top:2946px"></span>
<h2 class="h2 light" style="left:113px;top:2976px">Human Care Powered<br>by Technology</h2>
<p class="abs" style="left:113px;top:3117px;color:#fff;font-size:25px;font-weight:400">All Your Mind Body Needs Met In One Place</p>
<p class="body" style="left:113px;top:3176px;width:560px;color:#fff">All practitioners work collaboratively to provide the best care.</p>

<div class="band" style="top:3360px" role="img" aria-label="Decorative band of triangles and half circles in orange and tan"></div>

<!-- TESTIMONIALS -->
<div class="cream" style="top:3406px;height:623px"></div>
<span class="leaf" style="left:594px;top:3508px"></span>
<h2 class="h2" style="left:0;top:3537px;width:1200px;text-align:center">Our Testimonials</h2>
<svg class="arrow" style="left:66px" viewBox="0 0 20 30"><path d="M16 3L4 15l12 12" stroke="var(--gold)" stroke-width="4" fill="none"/></svg>
<svg class="arrow" style="left:1106px" viewBox="0 0 20 30"><path d="M4 3l12 12L4 27" stroke="var(--gold)" stroke-width="4" fill="none"/></svg>
<article class="quote" style="left:107px">
  <div class="avatar" role="img" aria-label="Portrait photo of the reviewer"></div>
  <h3>CARRIE | FIELD OPERATIONS</h3>
  <time>April 11, 2016</time>
  <p>I had no idea that being healthy would actually be this easy and fun. Workouts and nutrition used to be a source of stress for me. It's so interesting how proper knowledge and techniques can change everything!</p>
</article>
<article class="quote" style="left:614px">
  <div class="avatar" role="img" aria-label="Portrait photo of the reviewer"></div>
  <h3 style="top:28px">IRIS | ACCOUNTING</h3>
  <time style="top:64px">June 26, 2016</time>
  <p style="top:113px">I'm so glad that I chose Veridia for our company. Who knew that something that I could just expense from petty cash would transform the lives of so many people here including myself.</p>
</article>

<div class="band" style="top:4028px" role="img" aria-label="Decorative band of triangles and half circles in orange and tan"></div>

<!-- CONTACT -->
<div class="dark" style="top:4074px;height:690px" role="img" aria-label="Dark photograph of white blossoms"></div>
<span class="leaf" style="left:115px;top:4235px"></span>
<h2 class="h2 light" style="left:113px;top:4252px">We'd Love To Hear<br>From You</h2>
<p class="abs" style="left:113px;top:4378px;width:400px;color:#fff;font-size:16px;line-height:30px;font-weight:300">Tell us a little about you and your company to see if you qualify for our membership-based model at no cost to your company.</p>
<p class="abs" style="left:116px;top:4498px;color:#fff;font-size:17px;text-decoration:underline;font-family:'Roboto',sans-serif">
  <svg width="18" height="14" viewBox="0 0 18 14" style="vertical-align:-1px;margin-right:8px"><rect x="1" y="1" width="16" height="12" fill="none" stroke="#fff" stroke-width="1.5"/><path d="M1 1l8 7 8-7" fill="none" stroke="#fff" stroke-width="1.5"/></svg>hello@oruna.com</p>

<form>
  <div class="field" style="top:4212px">Name</div>
  <div class="field" style="top:4273px">Email</div>
  <div class="field" style="top:4335px">How many People in your location?</div>
  <div class="field" style="top:4397px">How many locations?</div>
  <div class="field" style="top:4459px;height:144px">Anything else we can help you with?</div>
  <a class="btn" style="left:886px;top:4625px;width:156px;height:45px">Submit Now</a>
</form>

<!-- FOOTER -->
<footer class="abs" style="left:0;top:4763px;width:1200px;height:258px;background:#141210">
  <div class="logo" style="left:113px;top:66px">
    <span class="dot" style="width:66px;height:66px"></span>
    <span class="name" style="font-size:50px">ORUNA</span>
  </div>
  <div class="abs" style="left:471px;top:72px;width:396px;height:49px;background:#fff;border-radius:25px;padding:15px 22px;font-size:14px;color:#1d1a16;font-family:'Roboto',sans-serif">Enter your email</div>
  <a class="btn" style="left:886px;top:72px;width:156px;height:49px">Submit Now</a>
  <p class="abs" style="left:477px;top:158px;color:#fff;font-size:14px;font-family:'Roboto',sans-serif">2025 Copyright - &nbsp;ORUNA | All Rights Reserved</p>
</footer>
<span class="social" style="left:885px"></span>
<span class="social" style="left:926px"></span>
<span class="social" style="left:967px"></span>
<span class="social" style="left:1008px"></span>

</body>
</html>
```